Vexa - Booking activities for Kids and Adults.

The app allows booking of Kid's activities for a given date/time.
The app lists activities offered via various clubs (vendors) which a user can book for their kids.
The users can browse various clubs and their offered activities. The users can manage their kid's profiles.
Need a whole new look to the app. The existing app can be checked out at
https://apps.storefrontexample.test/details?id=com.vexakw
https://apps.appmarketexample.test/us/app/vexa-فيكسا/id7302958146?ls=1
Try using the app as Guest.

Target Market(s)

Kuwait

Font styles to use
Serif
Sans Serif

Requirements
Must have
• Home Screens
The home page should have everything from the existing app and a quick area to change between different kid's profile to see activities matching their interests ONLY. In the current version, there's no switch profile and hence we are showing the name tags on the activities.

We are also going to build ecommerce so we need that ecommerce look and feel.
Kindly maintain the image aspect ratio from the current app so the new version doesn't require new images.

Need a complete new innovative designs - Keep the color scheme same.
The designs should be minimalistic and image oriented. The design should be done in XD. The designs should be submitted in both light and dark theme.
Reference to be used - http://plimtor.example

D.M for more info if needed.

```html
<!DOCTYPE html>
<html lang="en">
<head>
<meta charset="utf-8">
<title>Vexa – What's On</title>
<link href="https://fonts.googleapis.com/css2?family=Poppins:wght@400;500;600;700;800&display=swap" rel="stylesheet">
<style>
  :root{
    --bg:#f0f1f9;
    --white:#ffffff;
    --ink:#474262;
    --ink-soft:#5b5774;
    --orange:#f7931e;
    --teal:#00dcdc;
    --pin:#00c8c8;
    --tag-blue:#5aaaf0;
    --tag-pink:#f0508c;
    --heart:#f05a5a;
    --field:#eceef8;
    --pill:#f0f0f5;
  }
  *{box-sizing:border-box;margin:0;padding:0}
  html,body{width:1200px;height:2591px;overflow:hidden}
  body{background:var(--bg);font-family:"Poppins",sans-serif;color:var(--ink);position:relative}
  .abs{position:absolute}

  .header{left:0;top:0;width:1200px;height:455px;background:var(--white);border-radius:0 0 96px 96px;box-shadow:0 6px 30px rgba(80,80,140,.06)}
  .menu-dots{left:62px;top:204px;display:flex;gap:10px}
  .menu-dots span{width:18px;height:18px;border-radius:50%;background:var(--ink)}
  .brand{left:0;width:1200px;top:140px;text-align:center;font-size:120px;font-weight:500;color:var(--orange);line-height:1;letter-spacing:-2px}
  .cart{left:974px;top:188px}
  .cart-badge{left:1031px;top:192px;width:28px;height:28px;border-radius:50%;background:var(--orange);color:#fff;font-size:17px;font-weight:700;text-align:center;line-height:28px}
  .filter{left:1084px;top:196px}

  .search{left:64px;top:306px;width:1074px;height:101px;border-radius:51px;background:var(--field);box-shadow:0 8px 18px rgba(70,70,130,.12)}
  .search-text{left:134px;top:326px;font-size:42px;color:var(--ink);line-height:60px}
  .search-btn{left:1045px;top:313px;width:86px;height:86px;border-radius:50%;background:var(--orange);display:flex;align-items:center;justify-content:center;box-shadow:0 4px 10px rgba(200,110,0,.3)}

  .tab-dot{left:123px;top:493px;width:16px;height:16px;border-radius:50%;background:var(--teal)}
  .tabs{top:521px;font-size:42px;line-height:60px;color:var(--ink-soft);white-space:nowrap}
  .tab-active{font-weight:700;color:var(--ink)}

  .date-field{left:64px;top:614px;width:1074px;height:99px;border-radius:50px;background:var(--white);box-shadow:0 6px 16px rgba(70,70,130,.08)}
  .date-text{left:132px;top:640px;font-size:35px;line-height:48px;color:var(--ink)}
  .date-icon{left:1043px;top:645px}

  .card{left:61px;width:1080px;background:var(--white);border-radius:28px;overflow:hidden;box-shadow:0 10px 30px rgba(70,70,130,.06)}
  .card-media{width:100%;height:482px;position:relative}
  .media-kitchen{background:linear-gradient(120deg,#6b5a4a 0%,#a07850 30%,#2c6fb6 55%,#e9e2d8 80%,#c9b89a 100%)}
  .media-field{background:linear-gradient(180deg,#5a6e3a 0%,#2f6fc4 40%,#2a62b8 70%,#6f8a3e 100%)}
  .tag{position:absolute;top:47px;height:41px;border-radius:21px;color:#fff;font-size:22px;font-weight:700;line-height:41px;text-align:center}
  .tag-blue{background:var(--tag-blue)}
  .tag-pink{background:var(--tag-pink)}
  .heart{position:absolute;right:28px;top:38px;width:68px;height:68px;border-radius:50%;display:flex;align-items:center;justify-content:center}
  .heart-filled{background:var(--heart)}
  .heart-light{background:var(--white)}
  .card-title{position:absolute;left:70px;font-size:48px;font-weight:700;line-height:64px;color:var(--ink);white-space:nowrap}
  .meta{position:absolute;left:71px;display:flex;align-items:center;font-size:28px;line-height:40px;color:var(--ink);white-space:nowrap}
  .meta svg{margin-right:7px}
  .meta .gap{margin-left:16px}
  .vendor{position:absolute;left:67px;width:228px;height:35px;border-radius:18px;background:var(--pill);font-size:18px;line-height:35px;text-align:center;color:var(--ink);white-space:nowrap}
  .price{position:absolute;left:319px;font-size:40px;font-weight:700;color:var(--orange);line-height:50px;white-space:nowrap}
  .book{position:absolute;left:849px;width:199px;height:54px;border-radius:27px 27px 27px 6px;background:var(--orange);color:#fff;font-size:32px;font-weight:700;text-align:center;line-height:54px;letter-spacing:.5px}

  .nav{left:5px;top:2389px;width:1192px;height:202px;background:var(--teal);border-radius:104px}
  .nav-item{position:absolute;top:2420px;width:240px;text-align:center;color:#fff;font-size:32px;font-weight:700;white-space:nowrap}
  .nav-icon{height:88px;display:flex;align-items:center;justify-content:center}
  .nav-icon-active{width:86px;height:78px;margin:5px auto;border-radius:8px;background:var(--orange);display:flex;align-items:center;justify-content:center}
  .nav-label{margin-top:8px;line-height:40px}
</style>
</head>
<body>

<header class="abs header"></header>
<div class="abs menu-dots"><span></span><span></span><span></span></div>
<div class="abs brand">Vexa</div>

<svg class="abs cart" width="74" height="66" viewBox="0 0 74 66" fill="none" stroke="#474262" stroke-width="5" stroke-linejoin="round" stroke-linecap="round">
  <path d="M22 24 L37 6 L52 24"/>
  <path d="M4 24 H70 V34 H4 Z"/>
  <path d="M8 34 L14 60 H60 L66 34"/>
  <path d="M26 42 V52 M37 42 V52 M48 42 V52"/>
</svg>
<div class="abs cart-badge">0</div>
<svg class="abs filter" width="56" height="56" viewBox="0 0 56 56" fill="none" stroke="#474262" stroke-width="4.5" stroke-linejoin="round">
  <path d="M3 4 H53 L33 28 V50 L23 44 V28 Z"/>
</svg>

<div class="abs search"></div>
<div class="abs search-text">Search...</div>
<div class="abs search-btn">
  <svg width="34" height="34" viewBox="0 0 34 34" fill="none" stroke="#fff" stroke-width="4" stroke-linecap="round"><circle cx="14" cy="14" r="10"/><path d="M22 22 L30 30"/></svg>
</div>

<div class="abs tab-dot"></div>
<div class="abs tabs tab-active" style="left:61px">Today</div>
<div class="abs tabs" style="left:296px">Yesterday</div>
<div class="abs tabs" style="left:603px">Last Week</div>
<div class="abs tabs" style="left:913px">Last Month</div>

<div class="abs date-field"></div>
<div class="abs date-text">Pick a date</div>
<svg class="abs date-icon" width="40" height="40" viewBox="0 0 40 40" fill="none" stroke="#7a7790" stroke-width="2.5">
  <rect x="3" y="6" width="34" height="31" rx="3"/><path d="M3 13 H37 M11 2 V9 M29 2 V9"/>
  <path d="M10 19h3M18 19h3M26 19h3M10 25h3M18 25h3M26 25h3M10 31h3M18 31h3M26 31h3"/>
</svg>

<article class="abs card" style="top:772px;height:743px">
  <div class="card-media media-kitchen" role="img" aria-label="Parent and young child sharing fresh vegetables at a kitchen counter">
    <span class="tag tag-blue" style="left:62px;width:112px">SARA</span>
    <span class="tag tag-pink" style="left:182px;width:115px">FAHAD</span>
    <span class="heart heart-filled"><svg width="34" height="30" viewBox="0 0 34 30"><path d="M17 29 L3 15 A8 8 0 0 1 17 5 A8 8 0 0 1 31 15 Z" fill="#fff"/></svg></span>
  </div>
  <h2 class="card-title" style="top:532px">Cooking Classes for Beginners</h2>
  <div class="meta" style="top:597px">
    <svg width="20" height="26" viewBox="0 0 20 26"><path d="M10 1 A9 9 0 0 1 19 10 C19 17 10 25 10 25 C10 25 1 17 1 10 A9 9 0 0 1 10 1 Z" fill="#00c8c8"/><circle cx="10" cy="10" r="3.5" fill="#fff"/></svg>
    Hatten, Kuwait
    <svg class="gap" width="26" height="26" viewBox="0 0 26 26" fill="none" stroke="#00c8c8" stroke-width="2"><circle cx="13" cy="13" r="11"/><path d="M13 7 V13 L17 16"/></svg>
    10:00 am
    <svg class="gap" width="24" height="24" viewBox="0 0 24 24" fill="none" stroke="#00c8c8" stroke-width="2"><rect x="2" y="4" width="20" height="18" rx="2"/><path d="M2 9 H22 M7 13h2M11 13h2M15 13h2M7 17h2M11 17h2M15 17h2"/></svg>
    8-12 Years
  </div>
  <div class="vendor" style="top:653px">Warm Crust Academy</div>
  <div class="price" style="top:644px">KD 30.000</div>
  <div class="book" style="top:637px">BOOK</div>
</article>

<article class="abs card" style="top:1575px;height:742px">
  <div class="card-media media-field" role="img" aria-label="Three boys in blue football kits standing together on a grass pitch with a ball">
    <span class="tag tag-blue" style="left:62px;width:112px">SARA</span>
    <span class="heart heart-light"><svg width="34" height="30" viewBox="0 0 34 30"><path d="M17 29 L3 15 A8 8 0 0 1 17 5 A8 8 0 0 1 31 15 Z" fill="#f05a5a"/></svg></span>
  </div>
  <h2 class="card-title" style="top:532px">Junior Champions</h2>
  <div class="meta" style="top:596px">
    <svg width="20" height="26" viewBox="0 0 20 26"><path d="M10 1 A9 9 0 0 1 19 10 C19 17 10 25 10 25 C10 25 1 17 1 10 A9 9 0 0 1 10 1 Z" fill="#00c8c8"/><circle cx="10" cy="10" r="3.5" fill="#fff"/></svg>
    Hatten, Kuwait
    <svg class="gap" width="26" height="26" viewBox="0 0 26 26" fill="none" stroke="#00c8c8" stroke-width="2"><circle cx="13" cy="13" r="11"/><path d="M13 7 V13 L17 16"/></svg>
    10:00 am
    <svg class="gap" width="24" height="24" viewBox="0 0 24 24" fill="none" stroke="#00c8c8" stroke-width="2"><rect x="2" y="4" width="20" height="18" rx="2"/><path d="M2 9 H22 M7 13h2M11 13h2M15 13h2M7 17h2M11 17h2M15 17h2"/></svg>
    8-12 Years
  </div>
  <div class="vendor" style="top:653px">Warm Crust Academy</div>
  <div class="price" style="top:644px">KD 30.000</div>
  <div class="book" style="top:637px">BOOK</div>
</article>

<nav class="abs nav"></nav>
<div class="nav-item" style="left:108px">
  <div class="nav-icon"><div class="nav-icon-active">
    <svg width="50" height="50" viewBox="0 0 40 40" fill="none" stroke="#fff" stroke-width="2.6"><rect x="3" y="6" width="34" height="31" rx="3"/><path d="M3 13 H37 M11 2 V9 M29 2 V9 M10 19h3M18 19h3M26 19h3M10 25h3M18 25h3M26 25h3M10 31h3M18 31h3M26 31h3"/></svg>
  </div></div>
  <div class="nav-label">What's On</div>
</div>
<div class="nav-item" style="left:373px">
  <div class="nav-icon"><svg width="54" height="54" viewBox="0 0 34 34" fill="none" stroke="#fff" stroke-width="3.4" stroke-linecap="round"><circle cx="14" cy="14" r="11"/><path d="M22 22 L31 31"/></svg></div>
  <div class="nav-label">Search</div>
</div>
<div class="nav-item" style="left:627px">
  <div class="nav-icon"><svg width="48" height="62" viewBox="0 0 30 40" fill="none" stroke="#fff" stroke-width="3" stroke-linejoin="round"><path d="M3 3 H27 V37 L15 27 L3 37 Z"/></svg></div>
  <div class="nav-label">Saved</div>
</div>
<div class="nav-item" style="left:860px">
  <div class="nav-icon"><svg width="56" height="60" viewBox="0 0 36 40" fill="none" stroke="#fff" stroke-width="3" stroke-linecap="round"><circle cx="18" cy="12" r="9"/><path d="M3 38 C3 28 10 23 18 23 C26 23 33 28 33 38"/></svg></div>
  <div class="nav-label">Account</div>
</div>

</body>
</html>
```